A new updated business card. A good first impression for new customers to our business.

I need something unique. I will attached a picture of our old rubbish cards, and also our current Logo ( I think this needs an update if you have any ideas, its very basic and budget)The best way you will get to see my business is checking our Facebook page, I don't really know what else to say, but anything you want to know, ask away.www.facebook.com/tkwashandseal/

Target Market(s)

Home owners

Industry/Entity Type

Business

Contact Information for Business Card

T&K's Pressure Cleaning & Concrete Sealing
Maya 0492 615 370 maya@tkwashandseal.com
Dylan 0431 528 906 dylan@tkwashandseal.com

FB: www.facebook.com/tkwashandseal/
Website: www.tkwashandseal.net (This is pretty rubbish- we don't really use it)

100% customer satisfaction guaranteed

All aspects of Hi-Pressure Cleaning
Sealing & Re-Sealing
Roof Cleaning
Colour sealing
Decorative coatings

Free no obligation quotes

Requirements
Must have
• NO OBLIGATION FREE quotes
• 100% Customer satisfaction guaranteed
• Can you please add both names, contact details and email address on one card.
• Dylan 0431 528 906
• dylan@tkwashandseal.com
• Maya 0492 615 370
• maya@tkwashandseal.com
• Please change the services:
• Hot/Cold Hi-Pressure Cleaning
• Sealing & Re-Sealing
• Roof Cleaning
• Colour Sealing
• Decorative Coatings
• Concrete Honing
• Thanks
Nice to have
• Something a bit different, something eye catching.l

```html
<!DOCTYPE html>
<html lang="en">
<head>
<meta charset="utf-8">
<title>T&amp;K's Pressure Cleaning &amp; Concrete Sealing – Business Card</title>
<link href="https://fonts.googleapis.com/css2?family=Open+Sans:wght@400;600;700&display=swap" rel="stylesheet">
<style>
  :root{
    --red:#f20000;
    --white:#ffffff;
    --sky:#7fd0f0;
    --sky-light:#c9ecfa;
    --backdrop:#e9e6e3;
  }
  *{box-sizing:border-box;margin:0;padding:0}
  html,body{width:1200px;height:900px;overflow:hidden}
  body{background:var(--backdrop);font-family:"Open Sans",Arial,sans-serif;position:relative}
  .card{position:absolute;width:588px;height:364px;background:var(--white);overflow:hidden;box-shadow:0 4px 14px rgba(0,0,0,.18)}
  .card--front{left:78px;top:34px}
  .card--back{left:388px;top:505px}
  .card__band{position:absolute;left:0;top:0;width:588px;height:364px}
  .brand{position:absolute;left:0;right:0;top:40px;text-align:center;color:var(--red);font-weight:700;font-size:22px;line-height:1.2;text-transform:uppercase;letter-spacing:.2px}
  .brand__line{display:block}
  .contact{position:absolute;top:222px;color:var(--white);font-size:15px;line-height:1}
  .contact--left{right:318px;text-align:right}
  .contact--right{left:302px}
  .contact__name{font-weight:600;font-size:20px;margin-bottom:10px}
  .contact__row{display:flex;align-items:center;gap:8px;height:26px}
  .contact--left .contact__row{justify-content:flex-end}
  .contact__row--gap{margin-top:12px}
  .icon{width:13px;height:13px;flex:none;fill:var(--white)}
  .dot{width:10px;height:10px;border-radius:50%;background:var(--white);flex:none}
  .pitch{position:absolute;left:0;right:0;top:206px;color:var(--white);text-align:center}
  .pitch__headline{font-size:20px;font-weight:600;line-height:1.3;margin-bottom:4px}
  .pitch__quotes{font-size:15px;font-weight:700;text-transform:uppercase;letter-spacing:.3px;line-height:1.3;margin-bottom:10px}
  .services{display:grid;grid-template-columns:1fr 1fr;column-gap:30px;row-gap:6px;font-size:14px;font-weight:600;line-height:1.3}
  .services .l{text-align:right}
  .services .r{text-align:left}
  .bullet{display:inline-block;width:7px;height:7px;border-radius:50%;background:var(--white);vertical-align:middle;margin:0 4px 2px}
</style>
</head>
<body>

<section class="card card--front">
  <svg class="card__band" viewBox="0 0 588 364" aria-hidden="true">
    <defs>
      <linearGradient id="skyFront" x1="0" y1="0" x2="0" y2="1">
        <stop offset="0" stop-color="#c9ecfa"/><stop offset="1" stop-color="#7fd0f0"/>
      </linearGradient>
    </defs>
    <polygon points="0,188 400,188 382,212 0,212" fill="url(#skyFront)"/>
    <polygon points="412,178 588,178 588,364 0,364 0,216 384,216" fill="#f20000"/>
  </svg>
  <h1 class="brand"><span class="brand__line">T&amp;K's Pressure Cleaning</span><span class="brand__line">&amp; Concrete Sealing</span></h1>

  <div class="contact contact--left">
    <p class="contact__name">Maya</p>
    <p class="contact__row">0492 615 370 <svg class="icon" viewBox="0 0 24 24"><path d="M6.6 10.8a15 15 0 0 0 6.6 6.6l2.2-2.2a1 1 0 0 1 1-.25 11.4 11.4 0 0 0 3.6.57 1 1 0 0 1 1 1V20a1 1 0 0 1-1 1A17 17 0 0 1 3 4a1 1 0 0 1 1-1h3.5a1 1 0 0 1 1 1c0 1.25.2 2.45.57 3.57a1 1 0 0 1-.25 1z"/></svg></p>
    <p class="contact__row">maya@tkwashandseal.com <svg class="icon" viewBox="0 0 24 24"><path d="M2 5h20v14H2zm2 2v.5l8 5 8-5V7zm0 3v7h16v-7l-8 5z"/></svg></p>
    <p class="contact__row contact__row--gap">tkwashandseal <span class="dot"></span></p>
  </div>

  <div class="contact contact--right">
    <p class="contact__name">Dylan</p>
    <p class="contact__row"><svg class="icon" viewBox="0 0 24 24"><path d="M6.6 10.8a15 15 0 0 0 6.6 6.6l2.2-2.2a1 1 0 0 1 1-.25 11.4 11.4 0 0 0 3.6.57 1 1 0 0 1 1 1V20a1 1 0 0 1-1 1A17 17 0 0 1 3 4a1 1 0 0 1 1-1h3.5a1 1 0 0 1 1 1c0 1.25.2 2.45.57 3.57a1 1 0 0 1-.25 1z"/></svg> 0431 528 906</p>
    <p class="contact__row"><svg class="icon" viewBox="0 0 24 24"><path d="M2 5h20v14H2zm2 2v.5l8 5 8-5V7zm0 3v7h16v-7l-8 5z"/></svg> dylan@tkwashandseal.com</p>
    <p class="contact__row contact__row--gap"><svg class="icon" viewBox="0 0 24 24"><path d="M12 2a10 10 0 1 0 0 20 10 10 0 0 0 0-20zm6.9 6h-3a15 15 0 0 0-1.3-4 8 8 0 0 1 4.3 4zM12 4c.8 1.1 1.5 2.5 1.9 4h-3.8c.4-1.5 1.1-2.9 1.9-4zM4.3 14a8 8 0 0 1 0-4h3.3a16 16 0 0 0 0 4zm.8 2h3a15 15 0 0 0 1.3 4 8 8 0 0 1-4.3-4zm3-8h-3a8 8 0 0 1 4.3-4 15 15 0 0 0-1.3 4zM12 20c-.8-1.1-1.5-2.5-1.9-4h3.8c-.4 1.5-1.1 2.9-1.9 4zm2.3-6H9.7a14 14 0 0 1 0-4h4.6a14 14 0 0 1 0 4zm.3 6a15 15 0 0 0 1.3-4h3a8 8 0 0 1-4.3 4zm1.8-6a16 16 0 0 0 0-4h3.3a8 8 0 0 1 0 4z"/></svg> www.tkwashandseal.net</p>
  </div>
</section>

<section class="card card--back">
  <svg class="card__band" viewBox="0 0 588 364" aria-hidden="true">
    <defs>
      <linearGradient id="skyBack" x1="0" y1="0" x2="0" y2="1">
        <stop offset="0" stop-color="#c9ecfa"/><stop offset="1" stop-color="#7fd0f0"/>
      </linearGradient>
    </defs>
    <polygon points="0,172 362,172 344,196 0,196" fill="url(#skyBack)"/>
    <polygon points="374,162 588,162 588,364 0,364 0,200 346,200" fill="#f20000"/>
  </svg>
  <h2 class="brand"><span class="brand__line">T&amp;K's Pressure Cleaning</span><span class="brand__line">&amp; Concrete Sealing</span></h2>

  <div class="pitch">
    <p class="pitch__headline">100% customer satisfaction guaranteed</p>
    <p class="pitch__quotes">No obligation free quotes</p>
    <div class="services">
      <p class="l">Hot/Cold Hi-Pressure Cleaning <span class="bullet"></span></p>
      <p class="r"><span class="bullet"></span> Sealing &amp; Re-Sealing</p>
      <p class="l">Colour Sealing <span class="bullet"></span></p>
      <p class="r"><span class="bullet"></span> Roof Cleaning</p>
      <p class="l">Decorative Coatings <span class="bullet"></span></p>
      <p class="r"><span class="bullet"></span> Concrete Honing</p>
    </div>
  </div>
</section>

</body>
</html>
```